WordPress Website Design for Multi-Brand Aviation Group (Unified Branding System)

Project Overview:
We are seeking a professional, modern WordPress website design for an aviation-focused umbrella company that owns and operates multiple subsidiary businesses. The goal is to create a cohesive visual system that clearly communicates that each company operates under the same parent organization, while still allowing each brand to maintain a slightly distinct identity.
This is not just a single website design—we are looking for a scalable design framework that can be applied across multiple aviation-related businesses.
Objectives:
- Establish a consistent, recognizable brand identity across all company websites
Clearly communicate the relationship between the parent company and its subsidiaries
-bCreate a clean, high-end corporate aviation aesthetic
- Ensure all designs are SEO-friendly and optimized for performance
- Allow flexibility for future expansion (additional subsidiaries)
- Target Audience:
- Corporate aviation clients
- Charter customers
- Students wishing to receive flight training
- Aircraft owners and operators
- Turbine aircraft training to meet insurance requirements
- Business professionals and high-net-worth individuals
- Aviation industry partners
Design Direction & Style:
We are looking for a premium, professional aviation feel—think clean, modern, and high-trust. The design should reflect the standards of corporate aviation: precision, safety, and sophistication.
Key style notes:
Minimalist but impactful layout
High-quality aviation photography (jets, interiors, operations, global travel)
Subtle motion/interaction (hover effects, transitions)
Clear typography hierarchy for readability and professionalism
Branding Requirements:
Incorporate the primary colors of the parent company logo across all designs
Website Structure (Core Pages):
Design a system that includes:
Home Page with the following links:
- About / Company Overview
- Aircraft Management
- Aircraft Acquisition
- Charter
- Pilot Services
- Trip Support
- Contact Page
Site should further include:
- Mobile-first responsive design
- Fast-loading, performance-optimized layouts
SEO & Technical Considerations:
- Design should support high-level SEO implementation:
- Clean layout structure that translates well to semantic HTML
- Proper heading hierarchy (H1, H2, H3)
- Space for keyword-rich content without clutter
- Optimized image placement (with alt text capability)
- Fast load times (lightweight design approach)
- Compatibility with WordPress SEO plugins (e.g., Yoast or Rank Math)
WordPress Requirements:
- Design should be easily built using WordPress (preferred builders: Elementor, Gutenberg, or similar)
- Reusable templates for scalability across multiple sites
- Easy for non-developers to update text and images
- Modular components (blocks/sections that can be reused across pages and sites)
- Navigation & UX:
- Simple, intuitive navigation
- Sticky header preferred
Style guide including:
- Colors
- Fonts
- Button styles
- Layout system
- Designs similar to high-end corporate aviation, private jet charter, or luxury service brands are preferred—clean, sharp, and premium without being overly flashy.
What We Want to Avoid:
- Overly busy layouts
- Generic templates with no brand identity
- Outdated or “stock” looking aviation designs
- Poor mobile responsiveness
Additional Notes:
We are building a long-term brand system, not just a one-off website. There is potential for ongoing work as we expand additional subsidiary sites.
We value designers who understand branding consistency across multiple business units and can create a scalable, professional system.
Include the attached main company logo "Vireton Aviation Group" and the "Member PJFO" logo on the main page.

```html
<!DOCTYPE html>
<html lang="en">
<head>
<meta charset="utf-8">
<title>Vireton Aviation Group</title>
<link rel="stylesheet" href="https://fonts.googleapis.com/css2?family=Montserrat:wght@600;700;800;900&family=Poppins:wght@400;500;600;700&display=swap">
<style>
:root{
  --blue:#0b47a5;
  --blue-dark:#083a8c;
  --ink:#111827;
  --text:#3b4252;
  --muted:#5b6475;
  --light:#eaf2fb;
  --white:#ffffff;
  --footer-text:#d4e0f5;
}
*{box-sizing:border-box;margin:0;padding:0}
html,body{width:1200px;height:5177px;overflow:hidden}
body{font-family:"Poppins",sans-serif;color:var(--text);background:var(--white);position:relative}
.sec{position:absolute;left:0;width:1200px;overflow:hidden}
.abs{position:absolute}
h1,h2,h3{font-family:"Montserrat",sans-serif;font-weight:800;color:var(--ink);line-height:1.2}
.accent{color:var(--blue)}
.rule{position:absolute;width:42px;height:3px;background:var(--blue)}
.btn{position:absolute;display:flex;align-items:center;justify-content:center;background:var(--blue);color:var(--white);font-family:"Poppins",sans-serif;font-weight:600;font-size:11px;letter-spacing:.2px;border-radius:6px;text-transform:uppercase}
.btn.pill{border-radius:14px;font-size:9px}
p{font-size:12px;line-height:1.55}

/* header */
.header{top:0;height:122px;background:var(--white)}
.brand-name{font-family:"Montserrat",sans-serif;font-weight:800;color:var(--blue);font-size:27px;letter-spacing:1px;line-height:1}
.brand-sub{font-family:"Montserrat",sans-serif;font-weight:800;color:var(--blue);font-size:13px;letter-spacing:3.3px;margin-top:4px}
.call-label{font-size:11px;font-weight:600;color:var(--blue)}
.call-num{font-size:20px;font-weight:600;color:var(--blue)}
.nav{top:122px;height:38px;background:var(--blue)}
.nav ul{list-style:none;display:flex;position:absolute;left:152px;top:0;height:38px;align-items:center}
.nav li{color:var(--white);font-size:11.5px;font-weight:500;margin-right:26px;text-transform:uppercase}
.nav li.active{background:var(--white);color:var(--blue);padding:10px 6px;margin-right:20px}

/* hero */
.hero{top:160px;height:572px}
.hero-photo{position:absolute;inset:0;background:linear-gradient(180deg,#5b4a5a 0%,#c4623a 22%,#e9894a 36%,#8a6a78 52%,#2c3f6a 72%,#172744 100%)}
.hero h1{position:absolute;left:152px;top:270px;color:var(--white);font-size:41px;font-weight:900;letter-spacing:.5px;line-height:1.22}
.hero .lead{position:absolute;left:152px;top:390px;width:620px;color:var(--white);font-size:16px;line-height:1.6;font-weight:500}
.arrow{position:absolute;width:32px;height:32px;border:2px solid var(--white);border-radius:50%;display:flex;align-items:center;justify-content:center}

/* about */
.about{top:732px;height:540px}
.photo{position:absolute;border-radius:18px}
.about h2{position:absolute;left:652px;top:64px;font-size:30px}
.body-copy{position:absolute;font-size:12px;line-height:1.55;text-align:justify;color:var(--text)}

/* services */
.services{top:1270px;height:1308px;background:linear-gradient(180deg,#ffffff 0%,#e8f0fa 9%,#f5f8fc 30%,#f5f8fc 70%,#dfe6ee 100%)}
.services h2{position:absolute;left:0;width:1200px;text-align:center;top:162px;font-size:31px}
.card{position:absolute;width:281px;background:var(--white);border-radius:8px;box-shadow:0 4px 18px rgba(11,71,165,.08);text-align:center}
.card .icon{position:absolute;left:94px;top:32px;width:92px;height:92px}
.card h3{position:absolute;left:0;width:100%;top:150px;font-size:14.5px;font-weight:700;font-family:"Poppins",sans-serif;line-height:1.45;text-transform:uppercase}
.card p{position:absolute;left:36px;width:209px;font-size:11px;line-height:1.6;color:var(--muted)}
.card .btn{left:95px;width:90px;height:30px}
.card.featured{background:var(--blue)}
.card.featured h3,.card.featured p{color:var(--white)}
.card.featured .btn{background:var(--white);color:var(--blue)}
.jet-photo{position:absolute;left:0;top:1000px;width:1200px;height:308px;background:linear-gradient(180deg,rgba(245,248,252,0) 0%,#d6dee8 30%,#9aa7b6 62%,#5b6472 88%,#4a5260 100%)}

/* why */
.why{top:2578px;height:732px;background:var(--white)}
.why h2{position:absolute;left:155px;top:80px;font-size:31px;line-height:1.25}
.feature{position:absolute;left:150px;width:430px;height:80px}
.feature .ico{position:absolute;left:0;top:0;width:74px;height:74px;border-radius:50%;background:var(--white);box-shadow:0 4px 14px rgba(0,0,0,.12);display:flex;align-items:center;justify-content:center}
.feature h3{position:absolute;left:96px;top:6px;font-size:14px;font-weight:700;font-family:"Poppins",sans-serif}
.feature p{position:absolute;left:96px;top:28px;width:340px;font-size:11.5px;line-height:1.55;color:var(--muted)}

/* serving */
.serving{top:3310px;height:548px;background:var(--blue)}
.serving h2{position:absolute;left:648px;top:64px;font-size:31px;color:var(--white);line-height:1.28}
.serving .body-copy{color:var(--white)}
.list{position:absolute;left:648px;top:262px;list-style:none}
.list li{color:var(--white);font-size:12.5px;height:26px;display:flex;align-items:center}
.list li svg{margin-right:12px}

/* network */
.network{top:3858px;height:512px;background:var(--light)}
.network h2{position:absolute;left:155px;top:78px;font-size:31px;line-height:1.25}

/* cta */
.cta{top:4370px;height:442px}
.cta-photo{position:absolute;inset:0;background:linear-gradient(180deg,#334a78 0%,#7f88a6 30%,#c8a88f 50%,#58617e 70%,#1d2c52 100%)}
.frame{position:absolute;left:548px;top:70px;width:502px;height:346px;border:4px solid var(--white);border-left:none}
.frame::before{content:"";position:absolute;left:0;top:-4px;width:4px;height:82px;background:var(--white)}
.frame::after{content:"";position:absolute;left:0;bottom:-4px;width:4px;height:82px;background:var(--white)}
.cta h2{position:absolute;left:680px;top:120px;font-size:29px;color:var(--white);line-height:1.2}
.cta .lead{position:absolute;left:680px;top:210px;width:352px;font-size:14px;line-height:1.45;color:var(--white);font-weight:500}

/* footer */
.footer{top:4812px;height:365px;background:var(--blue-dark)}
.footer h4{position:absolute;font-size:12px;font-weight:600;color:var(--white);text-transform:uppercase}
.footer ul{position:absolute;list-style:none}
.footer ul li{color:var(--footer-text);font-size:11px;line-height:17.8px}
.contact-row{position:absolute;left:628px;display:flex;align-items:center;color:var(--footer-text);font-size:11px}
.contact-row svg{margin-right:14px}
.social{position:absolute;width:28px;height:28px;border-radius:50%;background:var(--white)}
.member{position:absolute;left:872px;top:164px;display:flex;align-items:center;color:var(--white);font-family:"Poppins",sans-serif;font-weight:500;font-size:20px;line-height:1}
.member .mark{display:block;width:20px;height:20px;background:var(--white);margin-right:12px}
.copy{position:absolute;left:0;width:1200px;top:330px;text-align:center;color:var(--footer-text);font-size:11px}
</style>
</head>
<body>

<header class="sec header">
  <div class="abs" style="left:152px;top:42px">
    <div class="brand-name">VIRETON</div>
    <div class="brand-sub">AVIATION GROUP</div>
  </div>
  <div class="btn" style="left:614px;top:34px;width:188px;height:44px;font-size:11px;border-radius:4px">Request Information</div>
  <svg class="abs" style="left:834px;top:40px" width="36" height="36" viewBox="0 0 36 36"><circle cx="18" cy="18" r="17" fill="#e8eef8"/><path d="M12 11c1-1 2-1 3 0l2 3c.5 1 0 2-1 2.5 1 2 2.5 3.5 4.5 4.5.5-1 1.5-1.5 2.5-1l3 2c1 1 1 2 0 3-2 2-5 1-9-3s-5-7-5-11z" fill="none" stroke="#0b47a5" stroke-width="1.6"/></svg>
  <div class="abs" style="left:886px;top:35px">
    <div class="call-label">CALL US NOW</div>
    <div class="call-num">+1 800 555 0142</div>
  </div>
</header>

<nav class="sec nav" aria-label="Main">
  <ul>
    <li class="active">Home</li>
    <li>About</li>
    <li>Aircraft Management</li>
    <li>Aircraft Acquisition</li>
    <li>Charter</li>
    <li>Pilot Services</li>
    <li>Trip Support</li>
    <li>Contact</li>
  </ul>
</nav>

<section class="sec hero">
  <div class="hero-photo" role="img" aria-label="Private jet flying above clouds at sunset"></div>
  <h1>PRECISION AVIATION<br>SERVICES. GLOBAL REACH.</h1>
  <p class="lead">Vireton Aviation Group delivers expert aircraft management, charter, acquisition, and trip support services.</p>
  <div class="btn" style="left:152px;top:470px;width:190px;height:44px;font-size:10.5px">Explore Our Services</div>
  <div class="btn" style="left:356px;top:470px;width:236px;height:44px;font-size:10.5px">Contact Our Aviation Team</div>
  <div class="arrow" style="left:962px;top:484px"><svg width="12" height="12" viewBox="0 0 12 12"><path d="M8 1L3 6l5 5" fill="none" stroke="#fff" stroke-width="1.8"/></svg></div>
  <div class="arrow" style="left:1014px;top:484px"><svg width="12" height="12" viewBox="0 0 12 12"><path d="M4 1l5 5-5 5" fill="none" stroke="#fff" stroke-width="1.8"/></svg></div>
</section>

<section class="sec about">
  <div class="photo" style="left:155px;top:65px;width:462px;height:452px;background:linear-gradient(180deg,#e9e2d6 0%,#d4bfa0 45%,#a88a66 80%,#7d6a55 100%)" role="img" aria-label="Private jet cabin interior with leather seats"></div>
  <h2>A UNIFIED <span class="accent">AVIATION<br>PLATFORM</span></h2>
  <div class="rule" style="left:652px;top:157px"></div>
  <p class="body-copy" style="left:652px;top:194px;width:382px">Vireton Aviation Group is the parent organization behind a network of specialized aviation companies. Each subsidiary operates with focused expertise while benefiting from the strength, infrastructure, and standards of the Vireton Aviation platform.</p>
  <p class="body-copy" style="left:652px;top:306px;width:382px">Our mission is simple: deliver seamless aviation services with the precision, reliability, and discretion expected in corporate aviation.</p>
  <p class="body-copy" style="left:652px;top:384px;width:382px">Whether you are an aircraft owner, charter client, aviation professional, or training candidate, Vireton Aviation connects you to a full ecosystem of aviation expertise.</p>
  <div class="btn" style="left:652px;top:474px;width:116px;height:38px;font-size:10px">Read More</div>
</section>

<section class="sec services">
  <h2>OUR <span class="accent">AVIATION</span> SERVICES</h2>
  <div class="rule" style="left:580px;top:234px"></div>

  <article class="card" style="left:151px;top:305px;height:357px">
    <svg class="icon" viewBox="0 0 92 92"><circle cx="46" cy="46" r="44" fill="#fff" stroke="#0b47a5" stroke-width="2"/><path d="M46 24l4 16 16 8v5l-16-4-1 12 5 4v4l-8-3-8 3v-4l5-4-1-12-16 4v-5l16-8z" fill="#0b47a5" transform="rotate(40 46 46)"/></svg>
    <h3>Integrated<br>Aviation Solutions</h3>
    <p style="top:208px">Vireton Aviation Group supports every stage of aircraft ownership and operation through a portfolio of specialized services.</p>
    <div class="btn pill" style="top:288px">Read More</div>
  </article>
  <article class="card featured" style="left:460px;top:305px;height:357px">
    <svg class="icon" viewBox="0 0 92 92"><circle cx="46" cy="46" r="44" fill="#fff"/><circle cx="46" cy="46" r="24" fill="none" stroke="#0b47a5" stroke-width="4" stroke-dasharray="6 3"/><circle cx="46" cy="46" r="14" fill="#0b47a5"/><path d="M40 48l12-8-4 12-2-4z" fill="#fff"/></svg>
    <h3>Aircraft<br>Management</h3>
    <p style="top:208px">Professional aircraft management designed to maximize operational efficiency while maintaining the highest standards of safety</p>
    <div class="btn pill" style="top:288px">Read More</div>
  </article>
  <article class="card" style="left:769px;top:305px;height:357px">
    <svg class="icon" viewBox="0 0 92 92"><circle cx="46" cy="46" r="44" fill="#fff" stroke="#0b47a5" stroke-width="2"/><path d="M46 20l18 7v14c0 12-8 20-18 24-10-4-18-12-18-24V27z" fill="#0b47a5"/><path d="M36 46l7 7 13-14" fill="none" stroke="#fff" stroke-width="4"/></svg>
    <h3>Aircraft<br>Acquisition</h3>
    <p style="top:208px">Strategic acquisition consulting that guides clients through aircraft selection, negotiation, and delivery with expert industry insight.</p>
    <div class="btn pill" style="top:288px">Read More</div>
  </article>

  <article class="card" style="left:151px;top:690px;height:320px">
    <svg class="icon" viewBox="0 0 92 92"><circle cx="46" cy="46" r="44" fill="#fff" stroke="#0b47a5" stroke-width="2"/><rect x="32" y="22" width="28" height="42" rx="3" fill="#0b47a5"/><path d="M37 32h18M37 39h18M37 46h18M37 53h12" stroke="#fff" stroke-width="2.4"/></svg>
    <h3 style="top:148px">Charter Services</h3>
    <p style="top:182px">Private jet charter solutions providing flexible, secure, and comfortable travel worldwide.</p>
    <div class="btn pill" style="top:252px">Read More</div>
  </article>
  <article class="card" style="left:460px;top:690px;height:320px">
    <svg class="icon" viewBox="0 0 92 92"><circle cx="46" cy="46" r="44" fill="#fff" stroke="#0b47a5" stroke-width="2"/><path d="M32 30h28l-3 8H35z" fill="#0b47a5"/><circle cx="46" cy="44" r="8" fill="#0b47a5"/><path d="M28 68c2-10 9-14 18-14s16 4 18 14z" fill="#0b47a5"/></svg>
    <h3 style="top:148px">Pilot Services</h3>
    <p style="top:182px">Experienced aviation professionals providing contract pilot support, crew placement, and operational expertise.</p>
    <div class="btn pill" style="top:252px">Read More</div>
  </article>
  <article class="card" style="left:769px;top:690px;height:320px">
    <svg class="icon" viewBox="0 0 92 92"><circle cx="46" cy="46" r="44" fill="#fff" stroke="#0b47a5" stroke-width="2"/><rect x="34" y="28" width="24" height="36" rx="4" fill="#0b47a5"/><path d="M41 28v-6h10v6" fill="none" stroke="#0b47a5" stroke-width="3"/><path d="M26 52l40-14" stroke="#0b47a5" stroke-width="3"/></svg>
    <h3 style="top:148px">Trip Support</h3>
    <p style="top:182px">Comprehensive global trip support services including flight planning, permits, fuel coordination, and ground logistics.</p>
    <div class="btn pill" style="top:252px">Read More</div>
  </article>

  <div class="jet-photo" role="img" aria-label="Business jet parked on a misty airport apron"></div>
</section>

<section class="sec why">
  <h2>WHY <span class="accent">AVIATION<br>PROFESSIONALS</span><br>TRUST VIRETON</h2>
  <div class="rule" style="left:155px;top:218px"></div>

  <div class="feature" style="top:270px">
    <div class="ico"><svg width="40" height="40" viewBox="0 0 40 40"><circle cx="20" cy="20" r="15" fill="none" stroke="#0b47a5" stroke-width="2.5"/><circle cx="20" cy="20" r="8" fill="#0b47a5"/><path d="M20 2v8M20 30v8M2 20h8M30 20h8" stroke="#0b47a5" stroke-width="2.5"/></svg></div>
    <h3>PRECISION OPERATIONS</h3>
    <p>Our aviation professionals maintain the highest operational standards across every service we provide.</p>
  </div>
  <div class="feature" style="top:370px">
    <div class="ico"><svg width="40" height="40" viewBox="0 0 40 40"><circle cx="20" cy="22" r="14" fill="none" stroke="#0b47a5" stroke-width="2.5"/><path d="M6 22h28M20 8c-6 8-6 20 0 28M20 8c6 8 6 20 0 28" fill="none" stroke="#0b47a5" stroke-width="2"/></svg></div>
    <h3>GLOBAL AVIATION NETWORK</h3>
    <p>We coordinate aviation operations across international destinations with experienced industry partners.</p>
  </div>
  <div class="feature" style="top:472px">
    <div class="ico"><svg width="40" height="40" viewBox="0 0 40 40"><path d="M20 4l13 5v10c0 9-6 15-13 18-7-3-13-9-13-18V9z" fill="#0b47a5"/><path d="M13 20l5 5 9-10" fill="none" stroke="#fff" stroke-width="3"/></svg></div>
    <h3>SAFETY FIRST</h3>
    <p>Safety, compliance, and operational discipline guide every flight operation and management decision.</p>
  </div>
  <div class="feature" style="top:582px">
    <div class="ico"><svg width="40" height="40" viewBox="0 0 40 40"><path d="M20 6l3 10 11 5v3l-11-3-1 8 4 3v2l-6-2-6 2v-2l4-3-1-8-11 3v-3l11-5z" fill="#0b47a5" transform="rotate(40 20 20)"/></svg></div>
    <h3>SEAMLESS AVIATION SOLUTIONS</h3>
    <p>From acquisition to operations, our integrated aviation platform simplifies complex aviation needs.</p>
  </div>

  <div class="photo" style="left:644px;top:87px;width:405px;height:574px;background:linear-gradient(180deg,#cfdbe6 0%,#9fb3c4 30%,#6c7f8c 55%,#7a6a45 78%,#3d3a2c 100%)" role="img" aria-label="Business jet flying over a golden landscape"></div>
</section>

<section class="sec serving">
  <div class="abs" style="left:0;top:0;width:610px;height:548px;background:linear-gradient(90deg,#5c7fa8 0%,#a9bdd4 45%,#6d8db3 85%,#0b47a5 100%)" role="img" aria-label="Aircraft cabin aisle with rows of seats"></div>
  <h2>SERVING THE GLOBAL<br>AVIATION COMMUNITY</h2>
  <div class="rule" style="left:648px;top:154px;background:#fff"></div>
  <p class="body-copy" style="left:648px;top:186px;width:390px;text-align:left">Vireton Aviation Group provides aviation solutions for a wide range of clients across the aviation industry.</p>
  <ul class="list">
    <li><svg width="8" height="12" viewBox="0 0 8 12"><path d="M1 1l5 5-5 5" fill="none" stroke="#fff" stroke-width="1.6"/></svg>Corporate aviation clients</li>
    <li><svg width="8" height="12" viewBox="0 0 8 12"><path d="M1 1l5 5-5 5" fill="none" stroke="#fff" stroke-width="1.6"/></svg>Private jet charter customers</li>
    <li><svg width="8" height="12" viewBox="0 0 8 12"><path d="M1 1l5 5-5 5" fill="none" stroke="#fff" stroke-width="1.6"/></svg>Aircraft owners and operators</li>
    <li><svg width="8" height="12" viewBox="0 0 8 12"><path d="M1 1l5 5-5 5" fill="none" stroke="#fff" stroke-width="1.6"/></svg>Flight training students</li>
    <li><svg width="8" height="12" viewBox="0 0 8 12"><path d="M1 1l5 5-5 5" fill="none" stroke="#fff" stroke-width="1.6"/></svg>Pilots requiring turbine training for insurance requirements</li>
    <li><svg width="8" height="12" viewBox="0 0 8 12"><path d="M1 1l5 5-5 5" fill="none" stroke="#fff" stroke-width="1.6"/></svg>Aviation industry partners</li>
    <li><svg width="8" height="12" viewBox="0 0 8 12"><path d="M1 1l5 5-5 5" fill="none" stroke="#fff" stroke-width="1.6"/></svg>Business professionals and high-net-worth individuals</li>
  </ul>
  <div class="btn" style="left:652px;top:452px;width:116px;height:38px;font-size:10px;background:#fff;color:var(--blue)">Read More</div>
</section>

<section class="sec network">
  <h2>A NETWORK OF<br><span class="accent">AVIATION SPECIALISTS</span></h2>
  <div class="rule" style="left:155px;top:163px"></div>
  <p class="body-copy" style="left:155px;top:198px;width:396px">Vireton Aviation Group oversees a portfolio of aviation companies that specialize in key areas of the aviation industry. Each company operates with focused expertise while benefiting from the shared standards and leadership of the Vireton Aviation brand.</p>
  <p class="body-copy" style="left:155px;top:310px;width:396px;text-align:left">Together, these companies create a unified aviation platform supporting aircraft ownership, operations, charter services, and aviation professionals.</p>
  <div class="btn" style="left:155px;top:395px;width:182px;height:38px;font-size:10.5px">View Our Companies</div>
  <div class="photo" style="left:600px;top:67px;width:450px;height:388px;background:linear-gradient(180deg,#c9ced6 0%,#8b929e 35%,#2c2f36 70%,#15171c 100%)" role="img" aria-label="Business jet cabin with black leather seats"></div>
</section>

<section class="sec cta">
  <div class="cta-photo" role="img" aria-label="Airliner flying through a dusk sky"></div>
  <div class="frame"></div>
  <h2>CONNECT WITH OUR<br>AVIATION TEAM</h2>
  <p class="lead">Whether you are exploring aircraft ownership, charter services, pilot support, or aviation partnerships, the team at Vireton Aviation Group is ready to assist.</p>
  <div class="btn" style="left:682px;top:302px;width:188px;height:38px;font-size:10.5px">Request Information</div>
</section>

<footer class="sec footer">
  <div class="abs" style="left:152px;top:78px">
    <div class="brand-name" style="color:#fff;font-size:34px">VIRETON</div>
    <div class="brand-sub" style="color:#fff;font-size:16px;letter-spacing:4.2px">AVIATION GROUP</div>
  </div>
  <div class="abs" style="left:155px;top:178px;color:#fff;font-size:12px;font-weight:600">FOLLOW US</div>
  <div class="social" style="left:262px;top:170px" role="img" aria-label="Social profile link 1"></div>
  <div class="social" style="left:295px;top:170px" role="img" aria-label="Social profile link 2"></div>
  <div class="social" style="left:328px;top:170px" role="img" aria-label="Social profile link 3"></div>
  <div class="social" style="left:361px;top:170px" role="img" aria-label="Social profile link 4"></div>

  <h4 style="left:460px;top:46px">Menu</h4>
  <ul style="left:462px;top:74px">
    <li>Home</li><li>About</li><li>Aircraft Management</li><li>Aircraft Acquisition</li><li>Charter</li><li>Pilot Services</li><li>Trip Support</li><li>Contact</li>
  </ul>

  <h4 style="left:628px;top:46px">Contact Us</h4>
  <div class="contact-row" style="top:78px"><svg width="10" height="14" viewBox="0 0 10 14"><path d="M5 0a5 5 0 015 5c0 4-5 9-5 9S0 9 0 5a5 5 0 015-5z" fill="#fff"/><circle cx="5" cy="5" r="2" fill="#083a8c"/></svg>1820 Runway Ave Suite 210 Mesa, AZ 85215</div>
  <div class="contact-row" style="top:104px"><svg width="12" height="9" viewBox="0 0 12 9"><rect x=".5" y=".5" width="11" height="8" fill="none" stroke="#fff"/><path d="M.5.5l5.5 4 5.5-4" fill="none" stroke="#fff"/></svg>sales@viretonaviation.example</div>
  <div class="contact-row" style="top:128px"><svg width="12" height="12" viewBox="0 0 12 12"><circle cx="6" cy="6" r="5.2" fill="none" stroke="#fff"/><path d="M6 3v3l2 1.5" fill="none" stroke="#fff"/></svg>Mon-Sun 8am-5pm</div>
  <div class="contact-row" style="top:152px"><svg width="12" height="12" viewBox="0 0 12 12"><path d="M2 1c.6-.6 1.2-.6 1.8 0l1.2 1.8c.3.6 0 1.2-.6 1.5.6 1.2 1.5 2.1 2.7 2.7.3-.6.9-.9 1.5-.6l1.8 1.2c.6.6.6 1.2 0 1.8-1.2 1.2-3 .6-5.4-1.8S.8 2.2 2 1z" fill="#fff"/></svg>+1 800 555 0142</div>

  <div class="member"><span class="mark"></span>Member PJFO</div>

  <div class="copy">Copyright © 2026 All Rights Reserved</div>
</footer>

</body>
</html>
```